develop our online residential property development appraisal service

This project requires a detailed WordPress design to represent a new digital residential property development consultancy business. At its heart it will have a number of different products that essentially advise customers of the potential value and feasibility of developing their residential site into multiple townhouses, units, apartments, etc... This will be accompanied by explaining the considerations of residential property development.

We aim to navigate and break down this complex area and provide our customers with the tools, knowledge, control and power to 'unlock the value' in their property.

REFERENCE DOCUMENTS:
1. Detailed solution requirements please refer to the attached 'wordpressdesignrequirements'
2. Logo files, style guide and colour pallet please refer to the attached 'KRLM.zip'
3. Site Map refer to attached 'wordpressdesignsitemap'

Reason: Additional information provided so extending period for designs to take into account.

Target Market(s)

The site will appeal to professional service providers; accountants, financial planners, lawyers, etc…

Industry/Entity Type

Residential

Font styles to use
Sans Serif
Other font styles liked:
• Similar to the logo font, slim line and simple

Requirements
Must have
• The logo, style and colour palette provided in the attached 'KRLM.zip' files
• Satisfy the intent of the 'wordpressdesignrequirements'
• Present as an online-centric business
• Clean, crisp and modern design
• Predominant use of white as a background contrasted with the colours provided in the colour palette
Nice to have
• Use of the following WordPress business themes is encouraged but not mandatory:
• 1. Mavo
• 2. Tulek
• 3. Vupa
Should not have
• Overt references to Australia

```html
<!DOCTYPE html>
<html lang="en">
<head>
<meta charset="utf-8">
<title>KRLM – Property Report Page A</title>
<link rel="stylesheet" href="https://fonts.googleapis.com/css2?family=Raleway:wght@200;300&family=Roboto:wght@400;500;700&display=swap">
<style>
  :root {
    --blue: #0a8fc9;
    --teal: #35aeae;
    --sea: #3aa86f;
    --green: #5cb646;
    --white: #ffffff;
    --quote-grey: #b7b7b7;
    --body-grey: #5a5a5a;
    --nav-ink: #222222;
    --footer: rgba(60, 60, 60, 0.9);
    --drawing-light: #f2f2f2;
    --drawing-mid: #d9d9d9;
  }
  * { margin: 0; padding: 0; box-sizing: border-box; }
  html, body { width: 895px; height: 1200px; overflow: hidden; background: var(--white); }
  .page { position: relative; width: 895px; height: 1200px; overflow: hidden; font-family: "Roboto", Arial, sans-serif; }

  .backdrop-drawing {
    position: absolute; left: 0; top: 640px; width: 895px; height: 560px;
    background: linear-gradient(180deg, rgba(242,242,242,0) 0%, var(--drawing-light) 25%, var(--drawing-mid) 100%);
  }

  .brand-band {
    position: absolute; left: 0; top: 49px; width: 895px; height: 93px;
    background: linear-gradient(90deg,
      #0a8fc9 0 78px, #0f97c2 78px 156px, #1ba0b4 156px 236px, #28a8a2 236px 316px,
      #36af8e 316px 400px, #45b47a 400px 520px, #52b864 520px 895px);
  }
  .brand {
    position: absolute; left: 34px; top: 74px; display: flex; align-items: center; color: var(--white);
  }
  .brand-name {
    font-family: "Raleway", Arial, sans-serif; font-weight: 200; font-size: 60px; letter-spacing: 2px; line-height: 1;
  }
  .brand-rule { width: 1px; height: 68px; background: var(--white); margin: 0 10px 0 14px; }
  .brand-tagline {
    font-family: "Raleway", Arial, sans-serif; font-weight: 300; font-size: 19px; line-height: 23px;
  }

  .nav-strip {
    position: absolute; left: 0; top: 142px; width: 440px; height: 110px;
    background: linear-gradient(180deg, #ffffff 70%, #f1f1f1 100%);
  }
  .main-nav { position: absolute; left: 21px; top: 206px; font-size: 13px; color: var(--nav-ink); letter-spacing: 0.3px; }
  .main-nav span { margin: 0 5px; }

  .hero-photo { position: absolute; left: 440px; top: -83px; }
  .page-badge {
    position: absolute; left: 334px; top: 142px; width: 186px; height: 186px; border-radius: 50%;
    background: rgba(53, 174, 174, 0.92); color: var(--white);
    display: flex; align-items: center; justify-content: center; text-align: center;
    font-size: 16px; font-weight: 500; line-height: 22px;
  }

  .column-divider { position: absolute; left: 421px; top: 330px; width: 1px; height: 600px; background: linear-gradient(180deg, #e6e6e6, rgba(230,230,230,0)); }

  .pull-quote {
    position: absolute; left: 70px; top: 312px; width: 284px; text-align: right;
    font-size: 20px; font-weight: 700; line-height: 26.6px; color: var(--quote-grey);
  }

  .page-links { position: absolute; left: 36px; top: 623px; display: flex; gap: 12px; }
  .page-link {
    width: 108px; height: 108px; border-radius: 50%; color: var(--white);
    display: flex; align-items: center; justify-content: center; text-align: center;
    font-size: 10px; font-weight: 700; line-height: 13px;
  }
  .page-link--email { background: var(--blue); }
  .page-link--b { background: var(--sea); }
  .page-link--c { background: var(--green); }

  .body-copy {
    position: absolute; left: 467px; top: 452px; width: 262px;
    font-size: 11.2px; font-weight: 500; line-height: 15px; color: var(--body-grey);
  }
  .body-copy p + p { margin-top: 15px; }

  .site-footer { position: absolute; left: 0; top: 1024px; width: 895px; height: 176px; background: var(--footer); color: #e6e6e6; }
  .footer-links { position: absolute; left: 45px; top: 99px; font-size: 11.5px; font-weight: 700; line-height: 15px; }
  .copyright { position: absolute; left: 382px; top: 130px; font-size: 7.5px; font-weight: 700; color: var(--white); }
  .social-links { position: absolute; left: 676px; top: 130px; display: flex; gap: 17px; }
  .social-dot { width: 14px; height: 14px; border-radius: 50%; background: var(--white); }
</style>
</head>
<body>
<div class="page">
  <div class="backdrop-drawing" role="img" aria-label="Faint line drawing of a multi-storey apartment building"></div>

  <div class="brand-band"></div>
  <div class="brand">
    <span class="brand-name">krlm</span>
    <span class="brand-rule"></span>
    <span class="brand-tagline">Residential Land Metrics<br>Consultancy</span>
  </div>

  <div class="nav-strip"></div>
  <nav class="main-nav">About Us<span>|</span>Social Media Integration<span>|</span>Contact Us</nav>

  <svg class="hero-photo" width="480" height="492" viewBox="0 0 480 492" role="img" aria-label="Photograph of a modern white apartment block with balconies, palm trees and a parked car">
    <defs>
      <linearGradient id="heroTones" x1="0" y1="0" x2="0" y2="1">
        <stop offset="0" stop-color="#e9eef2"/>
        <stop offset="0.45" stop-color="#b9bcb8"/>
        <stop offset="0.75" stop-color="#6f7d62"/>
        <stop offset="1" stop-color="#5b5e5a"/>
      </linearGradient>
    </defs>
    <circle cx="240" cy="240" r="240" fill="url(#heroTones)"/>
  </svg>

  <div class="page-badge">Property<br>Report<br>Page A</div>

  <div class="column-divider"></div>

  <p class="pull-quote">Proin cursus quis mauris id sollicitudin. Mauris et nulla eget dolor dictum posuere eget et lacus. Aenean convallis felis sed ultricies semper. Integer finibus egestas nisi, a tempus elit lacinia eget. Morbi tristique lacinia sagittis. Nullam ut enim in odio aliquam ultrices</p>

  <div class="page-links">
    <div class="page-link page-link--email">Email<br>Collection<br>Page</div>
    <div class="page-link page-link--b">Property<br>Report<br>Page B</div>
    <div class="page-link page-link--c">Property<br>Report<br>Page C</div>
  </div>

  <div class="body-copy">
    <p>Lorem Ipsum is simply dummy text of the printing and typesetting industry. Lorem Ipsum has been the industry's standard dummy text ever since the 1500s, when an unknown printer took a galley of type and scrambled it to make a type specimen book. It has survived not only five centuries, but also the leap into electronic typesetting, remaining essentially unchanged. It was popularised in the 1960s with the release of Typeleaf sheets containing Lorem Ipsum passages, and more recently with desktop publishing software like Pagewright Studio including versions of Lorem Ipsum.</p>
    <p>Contrary to popular belief, Lorem Ipsum is not simply random text. It has roots in a piece of classical Latin literature from 45 BC, making it over 2000 years old. Harold Brenwick, a Latin professor at Ashby-Moreland College in Carolina, looked up one of the more obscure Latin words, consectetur, from a Lorem Ipsum passage, and going through the cites of the word in classical literature, discovered the undoubtable source. Lorem Ipsum comes from sections 1.10.32 and 1.10.33 of "de Finibus Bonorum et Malorum" (The Extremes of Good and Evil) by Oratius, written in 45 BC. This book is a treatise on the theory of ethics, very popular during the Renaissance. The first line of Lorem Ipsum,</p>
  </div>

  <footer class="site-footer">
    <div class="footer-links">HOME<br>About Us<br>Site Map</div>
    <div class="copyright">Copyrights 2015 - All Rights Reserved</div>
    <div class="social-links" aria-label="Social links">
      <span class="social-dot"></span><span class="social-dot"></span><span class="social-dot"></span>
      <span class="social-dot"></span><span class="social-dot"></span><span class="social-dot"></span>
    </div>
  </footer>
</div>
</body>
</html>
```